8x8 Social Media Ad - Brant Summit Expo

Attention Real Estate Agents
Please join us for our
Quarterly Real Estate Training Expo
The 2nd Saturday of February, May, August and November
Our Next Training Expo is _________________________________
From 9 am to 1 pm
at
Halvorne Suites Millbrook Court
4817 Copper Willow Lane, Dunmere, MD 20588
Scheduled Speakers
9:00 am - Marcus Pellington - Orientation
9:30 am - Derrin Oakfield - Multiple Income Streams / Crest Program
10:00 am - Talia Brennick - Marketing though Social Media
10:45 am - Rex Dunmore - Generating Business through Ru-Plaza
11:30 am - Kemi Adeyoro - Real Estate Investing
12:15 pm - Gregor Tamsey - (Main Speaker) Training Topic TBA
For more information call Marcus Pellington at (240) 555-0183 or email mpellington@brantsummithomes.example

```html
<!DOCTYPE html>
<html lang="en">
<head>
<meta charset="utf-8">
<title>Brant Summit Expo – Quarterly Real Estate Training Expo</title>
<link rel="stylesheet" href="https://fonts.googleapis.com/css2?family=Poppins:wght@400;500;600;700;800&family=Oswald:wght@500;600&display=swap">
<style>
  :root {
    --teal: #0e8e98;
    --teal-deep: #0a6f77;
    --red: #d9080f;
    --ink: #222222;
    --black: #0b0b0b;
    --white: #ffffff;
    --backdrop: #bdbdbd;
  }
  * { margin: 0; padding: 0; box-sizing: border-box; }
  html, body { width: 1010px; height: 1200px; overflow: hidden; background: var(--backdrop); }
  body { position: relative; font-family: "Poppins", sans-serif; color: var(--ink); }

  .ad {
    position: absolute; left: 0; top: 95px;
    width: 1186px; height: 1186px;
    transform: scale(0.85160); transform-origin: 0 0;
    background: var(--white); overflow: hidden;
  }
  .abs { position: absolute; white-space: nowrap; }

  .crowd-panel {
    left: 873px; top: 0; width: 313px; height: 1083px;
    background: linear-gradient(180deg, #138a93 0%, #0f8088 55%, #0d7a82 100%);
  }
  .brand { left: 58px; top: 62px; display: flex; align-items: center; gap: 10px; }
  .brand-dot { width: 26px; height: 26px; background: var(--teal); }
  .brand-name { font-weight: 800; font-size: 34px; line-height: 1; color: var(--teal); letter-spacing: 1px; width: 210px; white-space: normal; }

  .headline { left: 338px; top: 52px; font-weight: 700; font-size: 88px; line-height: 1; color: var(--red); letter-spacing: 1px; }
  .subhead { left: 338px; top: 129px; font-weight: 600; font-size: 35px; line-height: 1; letter-spacing: 6.3px; color: var(--ink); }

  .join-band { left: 58px; top: 186px; width: 815px; height: 44px; background: var(--ink); color: var(--white);
    font-weight: 600; font-size: 38px; letter-spacing: 6.5px; line-height: 44px; padding-left: 20px; }

  .quarterly { left: 58px; top: 241px; font-weight: 700; font-size: 46px; line-height: 1.1; color: var(--teal); }
  .title { left: 56px; top: 289px; font-weight: 700; font-size: 74px; line-height: 70px; color: var(--ink); letter-spacing: -1px; }

  .dates { left: 56px; top: 443px; font-family: "Oswald", sans-serif; font-weight: 600; font-size: 32px; line-height: 1; color: var(--teal); letter-spacing: -0.9px; }
  .dates .hot { color: var(--red); }

  .next-box { left: 58px; top: 493px; width: 763px; height: 53px; border: 2px solid var(--ink); display: flex; }
  .next-label { background: var(--ink); color: var(--white); font-weight: 500; font-size: 22px; line-height: 49px; padding: 0 12px 0 8px; width: 305px; }

  .time-from { left: 58px; top: 564px; font-weight: 600; font-size: 20px; line-height: 1; }
  .time-range { left: 58px; top: 587px; font-weight: 700; font-size: 40px; line-height: 1; display: flex; align-items: center; gap: 6px; }
  .to-badge { width: 30px; height: 30px; border-radius: 50%; background: var(--teal); color: var(--white);
    font-size: 14px; font-weight: 600; line-height: 30px; text-align: center; }
  .divider { left: 311px; top: 570px; width: 2px; height: 68px; background: var(--teal); }
  .pin { left: 340px; top: 574px; }
  .venue { left: 406px; top: 570px; font-weight: 500; font-size: 17.5px; line-height: 24px; color: var(--ink); }

  .speakers-tab { left: 56px; top: 659px; }
  .speakers-tab-text { left: 68px; top: 661px; font-weight: 700; font-size: 36px; line-height: 46px; color: var(--white); }
  .speakers-rule { left: 543px; top: 700px; }

  .speaker { position: absolute; width: 400px; height: 110px; white-space: nowrap; }
  .speaker .photo { position: absolute; left: 0; top: 0; width: 104px; height: 104px; border-radius: 50%;
    border: 3px solid var(--teal); background: radial-gradient(circle at 50% 40%, #cfcfcf, #5a5a5a); overflow: hidden; }
  .speaker .name-tag { position: absolute; left: 104px; top: 2px; height: 29px; background: var(--teal);
    color: var(--white); font-weight: 700; font-size: 22px; line-height: 30px; padding: 0 20px 0 11px; border-radius: 0 4px 4px 0; }
  .speaker .topic { position: absolute; left: 115px; top: 36px; font-weight: 500; font-size: 16px; line-height: 19px; color: var(--ink); }
  .speaker .slot { position: absolute; left: 115px; font-weight: 700; font-size: 26px; line-height: 1; color: var(--ink); }

  .main-photo { left: 890px; top: 656px; width: 296px; height: 428px;
    background: linear-gradient(180deg, #0f8a93 0%, #2a2a2a 70%, #1d1d1d 100%); border-radius: 150px 150px 0 0; }
  .main-card { left: 476px; top: 964px; width: 420px; height: 104px; background: var(--teal); border: 2px solid var(--teal-deep); border-radius: 0 0 0 6px; }
  .main-label { left: 476px; top: 964px; }
  .main-label-text { left: 484px; top: 965px; font-weight: 600; font-size: 18px; line-height: 24px; color: var(--white); }
  .main-name { left: 491px; top: 991px; font-weight: 700; font-size: 37px; line-height: 1.1; color: var(--white); }
  .main-topic { left: 491px; top: 1035px; font-weight: 600; font-size: 16px; line-height: 1; color: var(--white); }

  .footer { left: 0; top: 1079px; width: 1186px; height: 107px; background: var(--black); color: var(--white);
    font-weight: 600; font-size: 17px; display: flex; align-items: center; align-self: flex-start; padding: 0 0 44px 58px; gap: 16px; white-space: nowrap; }
  .footer .item { display: flex; align-items: center; gap: 6px; }
</style>
</head>
<body>
  <main class="ad">
    <div class="abs crowd-panel" role="img" aria-label="Teal-tinted photo of an audience seated at a training event"></div>

    <div class="abs brand"><span class="brand-dot"></span><span class="brand-name">BRANT SUMMIT</span></div>
    <h1 class="abs headline">ATTENTION</h1>
    <p class="abs subhead">REAL ESTATE AGENTS</p>

    <p class="abs join-band">PLEASE JOIN US FOR OUR</p>
    <p class="abs quarterly">QUARTERLY</p>
    <h2 class="abs title">REAL ESTATE<br>TRAINING EXPO</h2>
    <p class="abs dates"><span class="hot">THE 2ND SATURDAY</span> OF FEBRUARY, MAY, AUGUST AND NOVEMBER</p>

    <div class="abs next-box"><span class="next-label">Our Next Training Expo is</span></div>

    <p class="abs time-from">FROM</p>
    <p class="abs time-range">9 AM <span class="to-badge">TO</span> 1 PM</p>
    <div class="abs divider"></div>
    <svg class="abs pin" width="52" height="60" viewBox="0 0 52 60" aria-hidden="true">
      <ellipse cx="26" cy="52" rx="22" ry="6" fill="none" stroke="var(--teal)" stroke-width="4"/>
      <path d="M26 2c-11 0-19 8-19 18 0 13 19 32 19 32s19-19 19-32C45 10 37 2 26 2z" fill="var(--teal)"/>
      <circle cx="26" cy="20" r="7" fill="var(--white)"/>
    </svg>
    <p class="abs venue">Halvorne Suites Millbrook Court<br>4817 Copper Willow Lane, Dunmere,<br>MD 20588</p>

    <svg class="abs speakers-tab" width="490" height="50" viewBox="0 0 490 50" aria-hidden="true">
      <polygon points="0,0 470,0 487,49 0,49" fill="var(--red)"/>
    </svg>
    <h3 class="abs speakers-tab-text">SCHEDULED SPEAKERS</h3>
    <svg class="abs speakers-rule" width="322" height="10" viewBox="0 0 322 10" aria-hidden="true">
      <line x1="4" y1="5" x2="316" y2="5" stroke="var(--ink)" stroke-width="2"/>
      <circle cx="317" cy="5" r="4.5" fill="var(--ink)"/>
    </svg>

    <div class="speaker" style="left:59px; top:731px;">
      <div class="photo" role="img" aria-label="Portrait of Marcus Pellington"></div>
      <span class="name-tag">MARCUS PELLINGTON</span>
      <p class="topic">Orientation</p>
      <p class="slot" style="top:58px;">9:00 AM</p>
    </div>
    <div class="speaker" style="left:480px; top:731px;">
      <div class="photo" role="img" aria-label="Portrait of Derrin Oakfield"></div>
      <span class="name-tag">DERRIN OAKFIELD</span>
      <p class="topic">Multiple Income Streams /<br>Crest Program</p>
      <p class="slot" style="top:76px;">9:30 AM</p>
    </div>
    <div class="speaker" style="left:59px; top:843px;">
      <div class="photo" role="img" aria-label="Portrait of Talia Brennick"></div>
      <span class="name-tag">TALIA BRENNICK</span>
      <p class="topic">Marketing through Social Media</p>
      <p class="slot" style="top:58px;">10:00 AM</p>
    </div>
    <div class="speaker" style="left:480px; top:843px;">
      <div class="photo" role="img" aria-label="Portrait of Rex Dunmore"></div>
      <span class="name-tag">REX DUNMORE</span>
      <p class="topic">Generating Business through<br>Ru-Plaza</p>
      <p class="slot" style="top:79px;">10:45 AM</p>
    </div>
    <div class="speaker" style="left:59px; top:955px;">
      <div class="photo" role="img" aria-label="Portrait of Kemi Adeyoro"></div>
      <span class="name-tag">KEMI ADEYORO</span>
      <p class="topic">Real Estate Investing</p>
      <p class="slot" style="top:58px;">11:30 AM</p>
    </div>

    <div class="abs main-card"></div>
    <div class="abs main-photo" role="img" aria-label="Portrait of main speaker Gregor Tamsey in a dark blazer"></div>
    <svg class="abs main-label" width="160" height="26" viewBox="0 0 160 26" aria-hidden="true">
      <polygon points="0,0 154,0 140,26 0,26" fill="var(--black)"/>
    </svg>
    <p class="abs main-label-text">Main Speaker</p>
    <p class="abs main-name">Gregor Tamsey</p>
    <p class="abs main-topic">Training Topic TBA &nbsp;·&nbsp; 12:15 PM</p>

    <footer class="abs footer">
      <span>For more information call Marcus Pellington at</span>
      <span class="item">
        <svg width="20" height="20" viewBox="0 0 22 22" aria-hidden="true">
          <circle cx="11" cy="11" r="9.5" fill="none" stroke="var(--teal)" stroke-width="2"/>
          <path d="M7.5 6.5c.6-.6 1.4-.5 1.8.1l1 1.5c.3.5.2 1-.2 1.4l-.6.5c.6 1.2 1.5 2.1 2.7 2.7l.5-.6c.4-.4 1-.5 1.4-.2l1.5 1c.6.4.7 1.2.1 1.8-1 1-2.6 1.2-4.2.3-1.8-1-3.3-2.5-4.3-4.3-.9-1.6-.7-3.2.3-4.2z" fill="var(--teal)"/>
        </svg>(240) 555-0183</span>
      <span class="item">
        <svg width="20" height="15" viewBox="0 0 22 16" aria-hidden="true">
          <rect x="1" y="1" width="20" height="14" fill="var(--teal)"/>
          <polyline points="1,1 11,9 21,1" fill="none" stroke="var(--black)" stroke-width="1.6"/>
        </svg>email mpellington@brantsummithomes.example</span>
    </footer>
  </main>
</body>
</html>
```